Business Card Design Project

looking for business cards with new logo

I am looking to keep with the colors of the logo i posted.  Here are some other details to consider.  I would like my website prominently displayed on the business card with the logo.  my website is www.HOmebaseTX.com...it should be spelled this way.

My contact information is:

Daniel R Whitcombe III
Broker/Owner
48531 Pellston Rd., Suite 307
Larkspur, Texas 78090
Office: 210-555-0147
Email:  Daniel@HOmebaseTX.com

Thank you
Daniel Whitcombe

Industry/Entity Type

Business

```html
<!DOCTYPE html>
<html lang="en">
<head>
<meta charset="utf-8">
<title>Homebase Realty – Business Card</title>
<link href="https://fonts.googleapis.com/css2?family=Open+Sans:wght@400;600;700&display=swap" rel="stylesheet">
<style>
  :root {
    --backdrop: #c9c5c1;
    --card-white: #ffffff;
    --card-black: #1c1c1c;
    --ink: #2a2a2a;
    --brand-blue: #3f8fd4;
    --rule: #333333;
    --ghost: rgba(63, 143, 212, 0.12);
  }
  * { margin: 0; padding: 0; box-sizing: border-box; }
  html, body {
    width: 1200px; height: 800px; overflow: hidden;
    background: var(--backdrop);
    font-family: "Open Sans", Arial, sans-serif;
    color: var(--ink);
  }
  .stage {
    width: 1200px; height: 800px;
    display: flex; align-items: center; justify-content: center; gap: 60px;
  }
  .card {
    position: relative;
    width: 525px; height: 300px;
    overflow: hidden;
    box-shadow: 0 6px 18px rgba(0,0,0,0.18);
  }
  .card-front { background: var(--card-white); }
  .card-back { background: var(--card-black); }
  .card-shapes { position: absolute; inset: 0; width: 100%; height: 100%; }

  /* front */
  .front-brand {
    position: absolute; left: 38px; top: 32px;
    display: flex; align-items: center; gap: 10px;
  }
  .brand-square { width: 14px; height: 14px; background: var(--brand-blue); }
  .front-brand .brand-name {
    font-size: 30px; font-weight: 600; color: var(--brand-blue); letter-spacing: -0.5px;
  }
  .front-brand-rule {
    position: absolute; left: 38px; top: 82px; width: 210px; height: 1px; background: var(--rule);
  }
  .contact { position: absolute; left: 38px; top: 98px; width: 300px; }
  .contact-name { font-size: 13px; font-weight: 700; color: var(--brand-blue); }
  .contact-name .contact-title { color: var(--ink); font-weight: 400; }
  .contact-line { font-size: 10.5px; line-height: 1.55; color: var(--ink); }
  .contact-rule { height: 1px; background: var(--rule); margin: 6px 0; }
  .contact-mail .at { color: var(--brand-blue); font-weight: 700; margin-right: 3px; }
  .website {
    position: absolute; left: 38px; top: 196px;
    font-size: 14px; font-weight: 700; color: var(--ink);
  }
  .website .site-name { color: var(--brand-blue); }
  .ghost-brand {
    position: absolute; right: 16px; top: 222px;
    font-size: 34px; font-weight: 600; color: var(--ghost); letter-spacing: -1px;
    white-space: nowrap;
  }

  /* back */
  .back-brand {
    position: absolute; inset: 0;
    display: flex; flex-direction: column; align-items: center; justify-content: center; gap: 14px;
  }
  .back-brand .brand-name {
    font-size: 46px; font-weight: 600; color: #ffffff; letter-spacing: -1px;
  }
  .back-brand-rule { width: 36px; height: 2px; background: #ffffff; }
</style>
</head>
<body>
<main class="stage">

  <section class="card card-front" aria-label="Business card front">
    <svg class="card-shapes" viewBox="0 0 525 300" aria-hidden="true">
      <polygon points="0,226 224,226 206,262 0,262" fill="var(--card-black)"/>
    </svg>

    <div class="front-brand">
      <span class="brand-square"></span>
      <span class="brand-name">Homebase Realty</span>
    </div>
    <div class="front-brand-rule"></div>

    <div class="contact">
      <p class="contact-name">Daniel R Whitcombe III <span class="contact-title">| Broker/Owner</span></p>
      <div class="contact-rule"></div>
      <p class="contact-line">48531 Pellston Rd., Suite 307 Larkspur, Texas 78090</p>
      <p class="contact-line contact-mail">210-555-0147 &nbsp;<span class="at">@</span>Daniel@HOmebaseTX.com</p>
      <div class="contact-rule"></div>
    </div>

    <p class="website">www.<span class="site-name">HOmebaseTX</span>.com</p>

    <p class="ghost-brand">Homebase Realty</p>
  </section>

  <section class="card card-back" aria-label="Business card back">
    <svg class="card-shapes" viewBox="0 0 525 300" aria-hidden="true">
      <polygon points="0,0 120,0 102,18 18,18 18,60 0,78" fill="var(--card-white)"/>
      <polygon points="525,300 405,300 423,282 507,282 507,240 525,222" fill="var(--card-white)"/>
    </svg>
    <div class="back-brand">
      <span class="brand-name">Homebase Realty</span>
      <span class="back-brand-rule"></span>
    </div>
  </section>

</main>
</body>
</html>
```